Coastal Learner Bureau business cards

Australian company about to start offering its services. We recruit international students to come to study English, vocational education and postgraduate courses in Australia. We help them find the institution and select the right city they want to come to Australia. We are a young, online oriented and supportive agency. Our clients are between 18 and 35 years old, mainly University students, young professionals or people with work experience. We provide much more information that any other agency offer. We administrate a Facebook group with more than 11.000 members that daily ask questions about general information when coming to Australia, while they are here and even after they leave the country

Target Market(s)

International students from South America, Central America and Europe

Industry/Entity Type

Student

Contact Information for Business Card

Tomas Bilbrea
Managing Director
tomas@kelvarin.com.au
www.kelvoria.com.au
+61 491058264
Melbourne, Australia

Font styles to use
Serif
Sans Serif

Colors

Designer to choose colors to be used in the design.

Requirements
Must have
• Horizontal design
• Standard business card size and shape. If font uses green or yellow colours, they will have to match the ones from the logo
Nice to have
• UPDATE: Use the contents of the green image to design one of the card sides. Use our logo in the background of that side as watermark.
• Passport image, or immigration stamps. A picture of the Yarra River (from Melbourne) would be cool as well.
Should not have
• Non-standard business card size and shape
• Not black as the background colour of any sides as we are not a VIP agency or a hight class service. We are orientes to young people and they like colours, pictures, something attractive.
• Vertical design
• NO YELLOW or BLACK AS THE BACKGROUND COLOUR OF ANY SIDE OF THE BIZ CARD

```html
<!DOCTYPE html>
<html lang="en">
<head>
<meta charset="utf-8">
<title>Coastal Learner Bureau business cards</title>
<link href="https://fonts.googleapis.com/css2?family=PT+Sans:wght@400;700&display=swap" rel="stylesheet">
<style>
  :root {
    --green: #17663f;
    --green-deep: #11553a;
    --yellow: #f0c419;
    --white: #ffffff;
    --paper: #f4f4f2;
    --backdrop: #e6e4df;
  }
  * { margin: 0; padding: 0; box-sizing: border-box; }
  html, body { width: 1200px; height: 886px; overflow: hidden; }
  body {
    background: var(--backdrop);
    font-family: "PT Sans", Arial, sans-serif;
    position: relative;
  }
  .card {
    position: absolute;
    width: 540px;
    height: 309px;
    border-radius: 18px;
    overflow: hidden;
    box-shadow: 0 10px 26px rgba(0,0,0,0.22);
  }
  .card-front {
    left: 40px; top: 150px;
    background: linear-gradient(135deg, var(--green) 0%, var(--green-deep) 100%);
    color: var(--white);
  }
  .brand {
    display: flex; align-items: center; gap: 12px;
    font-weight: 700; line-height: 1;
  }
  .brand-dot { width: 16px; height: 16px; border-radius: 50%; }
  .card-front .brand {
    position: absolute; left: 0; right: 0; top: 96px;
    justify-content: center; font-size: 62px; color: var(--white);
  }
  .card-front .brand-dot { background: var(--white); }
  .tagline {
    position: absolute; left: 60px; right: 60px; bottom: 52px;
    display: flex; align-items: center; gap: 10px;
    font-size: 15px; font-weight: 700;
  }
  .tagline::before, .tagline::after {
    content: ""; flex: 1; height: 1px; background: rgba(255,255,255,0.75);
  }
  .card-back {
    left: 620px; top: 420px;
    background: var(--paper);
  }
  .card-back .swoosh { position: absolute; inset: 0; }
  .card-back .brand {
    position: absolute; left: 38px; top: 116px;
    font-size: 48px; color: var(--green);
  }
  .card-back .brand-dot { width: 14px; height: 14px; background: var(--yellow); }
  .contact {
    position: absolute; right: 22px; top: 124px;
    text-align: right; color: var(--white);
    list-style: none;
  }
  .contact-name { font-size: 20px; font-weight: 700; color: var(--yellow); line-height: 1.1; }
  .contact-role { font-size: 14px; margin-bottom: 8px; }
  .contact-line {
    display: flex; justify-content: flex-end; align-items: center; gap: 7px;
    font-size: 12.5px; line-height: 1.55;
  }
  .icon { width: 12px; height: 12px; flex: none; }
</style>
</head>
<body>
  <section class="card card-front" aria-label="Card front">
    <div class="brand"><span class="brand-dot"></span>Kelvoria</div>
    <p class="tagline">Hacemos más por ti!</p>
  </section>

  <section class="card card-back" aria-label="Card back">
    <svg class="swoosh" viewBox="0 0 540 309" aria-hidden="true">
      <path d="M540,30 C400,36 320,60 290,150 C262,232 180,292 0,266 L0,286 C190,310 278,242 304,160 C332,80 410,50 540,48 Z" fill="var(--yellow)"/>
      <path d="M540,60 C420,64 342,82 314,162 C290,232 252,292 150,309 L540,309 Z" fill="var(--green)"/>
    </svg>
    <div class="brand"><span class="brand-dot"></span>Kelvoria</div>
    <ul class="contact">
      <li class="contact-name">Tomas Bilbrea</li>
      <li class="contact-role">Managing Director</li>
      <li class="contact-line">+61 491058264
        <svg class="icon" viewBox="0 0 12 12"><path d="M2.5 1 L4.5 1 L5.3 3.5 L4 4.6 C4.7 6 6 7.3 7.4 8 L8.5 6.7 L11 7.5 L11 9.5 C11 10.3 10.3 11 9.5 11 C5 11 1 7 1 2.5 C1 1.7 1.7 1 2.5 1 Z" fill="var(--yellow)"/></svg>
      </li>
      <li class="contact-line">tomas@kelvarin.com.au
        <svg class="icon" viewBox="0 0 12 12"><rect x="0.5" y="2.5" width="11" height="7.5" rx="1" fill="var(--yellow)"/><path d="M1 3 L6 7 L11 3" stroke="var(--green)" stroke-width="1" fill="none"/></svg>
      </li>
      <li class="contact-line">www.kelvoria.com.au
        <svg class="icon" viewBox="0 0 12 12"><circle cx="6" cy="6" r="5.5" fill="var(--yellow)"/><path d="M0.8 6 H11.2 M6 0.5 C3.5 3 3.5 9 6 11.5 M6 0.5 C8.5 3 8.5 9 6 11.5" stroke="var(--green)" stroke-width="0.9" fill="none"/></svg>
      </li>
      <li class="contact-line">Melbourne, Australia
        <svg class="icon" viewBox="0 0 12 12"><path d="M6 11.5 C3 7.8 2 6 2 4.3 A4 4 0 0 1 10 4.3 C10 6 9 7.8 6 11.5 Z" fill="var(--yellow)"/><circle cx="6" cy="4.4" r="1.5" fill="var(--green)"/></svg>
      </li>
    </ul>
  </section>
</body>
</html>
```